We are a recruitment company based in Norwich/Cambridge England.
I have included our company logo which we want to remain the same.

What we are looking for is a new creative Business card which will really stand out!!

Contact Information for Business Card

Harriet Dunmore
email: Harriet@plavex.co.uk
Address: Brackwell House
Fenmoor Enterprise Park
Partridge Way
Norwich
QB9 3KX
Tel:01632 960418

```html
<!DOCTYPE html>
<html lang="en">
<head>
<meta charset="utf-8">
<title>Plavex Business Card</title>
<link rel="stylesheet" href="https://fonts.googleapis.com/css2?family=Lato:wght@400;700&display=swap">
<style>
  :root {
    --page: #ecebe8;
    --card-front: #ffffff;
    --card-back: #8a898e;
    --brand-green: #7cc242;
    --brand-grey: #8b8a8f;
    --ink-light: #ffffff;
  }
  * { box-sizing: border-box; margin: 0; padding: 0; }
  html, body {
    width: 1200px; height: 1200px; overflow: hidden;
    background: var(--page);
    font-family: "Lato", sans-serif;
  }
  .canvas {
    position: relative; width: 1200px; height: 1200px;
  }
  .card {
    position: absolute; left: 220px; width: 760px; height: 434px;
    box-shadow: 0 6px 18px rgba(0,0,0,0.12);
  }
  .card--front { top: 110px; background: var(--card-front); }
  .card--back { top: 650px; background: var(--card-back); color: var(--ink-light); }

  .brand {
    position: absolute; left: 0; right: 0; top: 170px;
    display: flex; align-items: center; justify-content: center; gap: 22px;
  }
  .brand__dot {
    width: 70px; height: 70px; border-radius: 50%; background: var(--brand-grey);
  }
  .brand__name {
    font-weight: 700; font-size: 84px; color: var(--brand-green); letter-spacing: -1px;
    line-height: 1;
  }

  .rule { position: absolute; height: 2px; background: var(--ink-light); }
  .rule--top { top: 108px; left: 40px; width: 340px; }
  .rule--mid { top: 252px; left: 40px; width: 680px; }

  .back-brand {
    position: absolute; left: 400px; top: 72px;
    display: flex; align-items: center; gap: 12px;
  }
  .back-brand__dot { width: 40px; height: 40px; border-radius: 50%; background: var(--ink-light); }
  .back-brand__name { font-weight: 700; font-size: 46px; line-height: 1; }

  .holder {
    position: absolute; left: 60px; top: 140px;
    font-size: 42px; font-weight: 400;
  }
  .contact { position: absolute; left: 420px; top: 160px; font-size: 28px; }
  .contact__row { display: flex; align-items: center; gap: 12px; height: 40px; }
  .contact__icon { width: 22px; height: 22px; flex: none; }

  .web {
    position: absolute; left: 0; right: 0; top: 272px;
    text-align: center; font-size: 30px;
  }
  .address {
    position: absolute; left: 0; right: 0; top: 322px;
    text-align: center; font-size: 22px; line-height: 1.45;
  }
</style>
</head>
<body>
<main class="canvas">
  <section class="card card--front" aria-label="Card front">
    <div class="brand">
      <span class="brand__dot"></span>
      <span class="brand__name">Plavex</span>
    </div>
  </section>

  <section class="card card--back" aria-label="Card back">
    <div class="rule rule--top"></div>
    <div class="back-brand">
      <span class="back-brand__dot"></span>
      <span class="back-brand__name">Plavex</span>
    </div>
    <h1 class="holder">Harriet Dunmore</h1>
    <div class="contact">
      <div class="contact__row">
        <svg class="contact__icon" viewBox="0 0 24 24" aria-hidden="true">
          <path fill="#fff" d="M6.6 10.8a15.1 15.1 0 0 0 6.6 6.6l2.2-2.2a1 1 0 0 1 1-.25 11.4 11.4 0 0 0 3.6.57 1 1 0 0 1 1 1V20a1 1 0 0 1-1 1A17 17 0 0 1 3 4a1 1 0 0 1 1-1h3.5a1 1 0 0 1 1 1c0 1.25.2 2.45.57 3.57a1 1 0 0 1-.25 1z"/>
        </svg>
        <span>01632 960418</span>
      </div>
      <div class="contact__row">
        <svg class="contact__icon" viewBox="0 0 24 24" aria-hidden="true">
          <rect x="2" y="5" width="20" height="14" fill="#fff"/>
          <path d="M2 5l10 8 10-8" fill="none" stroke="#8a898e" stroke-width="1.6"/>
        </svg>
        <span>Harriet@plavex.co.uk</span>
      </div>
    </div>
    <div class="rule rule--mid"></div>
    <p class="web">www.plavex.co.uk</p>
    <p class="address">Brackwell House, Fenmoor Enterprise Park, Partridge Way,<br>Norwich, QB9 3KX</p>
  </section>
</main>
</body>
</html>
```